Creative, fresh business card design for Ripplecraft Facades

We need a fresh, creative business card design for Ripplecraft Facades. We are the manufacturer of Ripplecraft Facades in Australia. Wall panels are 2400 x 1200mm panels made from MDF and feature 3D patterns on the face of the panel. The colours to be used are green, silver/grey and white RGB
Red 187
Green 207
Blue 65.

An idea is to possibly use a watermark of one of our designs as a background (like on the "Grids" design on the left hand side of page 2 of our brochure).

Target Market(s)

Interior designers, architects, builders and home renovators

Industry/Entity Type

Business

Contact Information for Business Card

Details to go on the card are:
Our logo (attached),
Slogan: "Decorative panels for interiors and exteriors",
Contact name,
Position,
Mobile phone number,
Business address,
Business phone,
Business fax,
Website and
Email address.

I have attached a few images of our panels and our brochure for reference.

The colours of the business card should feature our logo colours which are: RGB
Red 187
Green 207
Blue 65

Requirements
Must have
• Very modern fonts and design. Some of the designs shown especially the "Prisms" design which is a popular design.
Nice to have
• Creative but simple design. Very contemporary.
Should not have
• Anything ornate or old fashioned.

```html
<!DOCTYPE html>
<html lang="en">
<head>
<meta charset="utf-8">
<title>Ripplecraft Facades – Business Cards</title>
<link rel="stylesheet" href="https://fonts.googleapis.com/css2?family=Cinzel:wght@400&family=Ubuntu:wght@400;700&display=swap">
<style>
  :root{
    --lime:#bbcf41;
    --grey:#8c8d8f;
    --stage:#8f8988;
    --ink:#231f20;
    --soft-ink:#4a4a4a;
    --white:#ffffff;
  }
  *{margin:0;padding:0;box-sizing:border-box}
  html,body{width:1017px;height:1200px;overflow:hidden}
  body{background:var(--stage);position:relative;font-family:"Ubuntu",sans-serif;color:var(--ink)}

  .card{position:absolute;left:58px;width:899px;height:473px;background:var(--white);overflow:hidden;
        box-shadow:0 22px 30px rgba(0,0,0,.28)}
  .card--plain{top:58px}
  .card--boxed{top:649px}

  .card__photo{position:absolute;left:0;top:0;width:450px;height:463px;
    background:linear-gradient(90deg,#4d4d4f 0%,#6d6d6f 45%,#9a9b9c 70%,#c9ccce 85%,#e4e4e2 100%)}
  .card__baseline{position:absolute;left:0;bottom:0;width:100%;height:10px;background:var(--lime)}

  .slogan-band{position:absolute;left:0;top:139px;width:570px;height:81px;background:var(--lime);
    padding:8px 0 0 70px;font-family:"Cinzel",serif;font-size:28.5px;line-height:33px;letter-spacing:.4px;color:var(--ink)}
  .slogan-band__rules{position:absolute;left:572px;top:139px;height:81px;width:20px;display:flex;gap:4px}
  .slogan-band__rules span{width:3px;height:100%;background:var(--lime)}

  .brand{position:absolute;left:634px;top:46px;display:flex;align-items:center;gap:8px}
  .brand__square{width:22px;height:22px;background:var(--lime)}
  .brand__name{font-size:17px;font-weight:700;color:var(--grey)}

  .person{position:absolute;left:600px;top:149px}
  .person__name{font-size:25px;font-weight:700;line-height:32px}
  .person__role{font-size:18px;color:var(--soft-ink);line-height:24px}

  .contact{position:absolute;left:594px;width:305px;padding-left:36px;font-size:16.5px;line-height:26.5px;color:var(--ink)}
  .contact__row{position:relative}
  .contact__icon{position:absolute;left:-26px;top:5px;width:18px;height:18px}
  .contact--address{top:232px}
  .contact--phones{top:294px}
  .contact--web{top:384px}

  .card--boxed .contact{padding-top:0}
  .card--boxed .contact--address{background:var(--grey);top:232px;height:55px}
  .card--boxed .contact--phones{background:var(--lime);top:296px;height:76px}
  .card--boxed .contact--web{background:var(--grey);top:382px;height:58px}
  .card--boxed .contact--address,.card--boxed .contact--web{padding-top:1px}
</style>
</head>
<body>

<svg width="0" height="0" style="position:absolute" aria-hidden="true">
  <defs>
    <symbol id="icon-pin" viewBox="0 0 20 20"><path d="M10 1a6 6 0 0 0-6 6c0 4.5 6 12 6 12s6-7.5 6-12a6 6 0 0 0-6-6zm0 8.5A2.5 2.5 0 1 1 10 4.5a2.5 2.5 0 0 1 0 5z" fill="currentColor"/></symbol>
    <symbol id="icon-mobile" viewBox="0 0 20 20"><rect x="5.5" y="1" width="9" height="18" rx="1.5" fill="none" stroke="currentColor" stroke-width="1.6"/><line x1="7.5" y1="15.5" x2="12.5" y2="15.5" stroke="currentColor" stroke-width="1.4"/></symbol>
    <symbol id="icon-phone" viewBox="0 0 20 20"><path d="M5 2l3 4-2 2c1 2.5 3.5 5 6 6l2-2 4 3-2 3C9 17 3 11 2 4z" fill="currentColor"/></symbol>
    <symbol id="icon-fax" viewBox="0 0 20 20"><rect x="5" y="2" width="10" height="6" fill="none" stroke="currentColor" stroke-width="1.5"/><rect x="1" y="8" width="18" height="9" rx="1.5" fill="currentColor"/><rect x="5" y="13" width="10" height="5" fill="#fff"/></symbol>
    <symbol id="icon-mail" viewBox="0 0 20 20"><rect x="2" y="4.5" width="16" height="11" fill="none" stroke="currentColor" stroke-width="1.5"/><path d="M2 4.5l8 6 8-6" fill="none" stroke="currentColor" stroke-width="1.5"/></symbol>
    <symbol id="icon-globe" viewBox="0 0 20 20"><g fill="none" stroke="currentColor" stroke-width="1.3"><circle cx="10" cy="10" r="8"/><ellipse cx="10" cy="10" rx="3.5" ry="8"/><line x1="2" y1="10" x2="18" y2="10"/><path d="M3.5 5.5h13M3.5 14.5h13"/></g></symbol>
  </defs>
</svg>

<!-- Card variant: open contact list -->
<section class="card card--plain">
  <div class="card__photo" role="img" aria-label="Photo of a wall clad in dark grey wave-patterned 3D panels beside a bright dining room with a lake view"></div>
  <div class="slogan-band">DECORATIVE PANELS FOR<br>INTERIORS AND EXTERIORS</div>
  <div class="slogan-band__rules"><span></span><span></span><span></span></div>

  <div class="brand"><span class="brand__square"></span><span class="brand__name">Ripplecraft Facades</span></div>

  <div class="person">
    <p class="person__name">Name comes here</p>
    <p class="person__role">designation here</p>
  </div>

  <div class="contact contact--address" style="color:var(--ink)">
    <p class="contact__row"><svg class="contact__icon" style="color:var(--lime)"><use href="#icon-pin"/></svg>48 Harbour Row Suite 12</p>
    <p class="contact__row">dummy, ABCD 30001</p>
  </div>
  <div class="contact contact--phones">
    <p class="contact__row"><svg class="contact__icon" style="color:var(--lime)"><use href="#icon-mobile"/></svg>020-5550173829</p>
    <p class="contact__row"><svg class="contact__icon" style="color:var(--lime)"><use href="#icon-phone"/></svg>0831-555204</p>
    <p class="contact__row"><svg class="contact__icon" style="color:var(--lime)"><use href="#icon-fax"/></svg>0128-555917</p>
  </div>
  <div class="contact contact--web">
    <p class="contact__row"><svg class="contact__icon" style="color:var(--lime)"><use href="#icon-mail"/></svg>hello@ripplecraft.example</p>
    <p class="contact__row"><svg class="contact__icon" style="color:var(--lime)"><use href="#icon-globe"/></svg>www.ripplecraft.example</p>
  </div>
  <div class="card__baseline"></div>
</section>

<!-- Card variant: boxed contact groups -->
<section class="card card--boxed">
  <div class="card__photo" role="img" aria-label="Photo of a wall clad in dark grey wave-patterned 3D panels beside a bright dining room with a lake view"></div>
  <div class="slogan-band">DECORATIVE PANELS FOR<br>INTERIORS AND EXTERIORS</div>
  <div class="slogan-band__rules"><span></span><span></span><span></span></div>

  <div class="brand"><span class="brand__square"></span><span class="brand__name">Ripplecraft Facades</span></div>

  <div class="person">
    <p class="person__name">Name comes here</p>
    <p class="person__role">designation here</p>
  </div>

  <div class="contact contact--address">
    <p class="contact__row"><svg class="contact__icon" style="color:var(--white)"><use href="#icon-pin"/></svg>48 Harbour Row Suite 12</p>
    <p class="contact__row">dummy, ABCD 30001</p>
  </div>
  <div class="contact contact--phones">
    <p class="contact__row"><svg class="contact__icon" style="color:var(--white)"><use href="#icon-mobile"/></svg>020-5550173829</p>
    <p class="contact__row"><svg class="contact__icon" style="color:var(--white)"><use href="#icon-phone"/></svg>0831-555204</p>
    <p class="contact__row"><svg class="contact__icon" style="color:var(--white)"><use href="#icon-fax"/></svg>0128-555917</p>
  </div>
  <div class="contact contact--web">
    <p class="contact__row"><svg class="contact__icon" style="color:var(--white)"><use href="#icon-mail"/></svg>hello@ripplecraft.example</p>
    <p class="contact__row"><svg class="contact__icon" style="color:var(--white)"><use href="#icon-globe"/></svg>www.ripplecraft.example</p>
  </div>
  <div class="card__baseline"></div>
</section>

</body>
</html>
```